A Gallery type Web design

We are developing a Wordpress based website for a client that does design construction projects. E.g. Pools, Lobbies, Toilets, etc. The website will mainly be to showcase their past projects and the collections they have.
No programming required, we just need the designs!
A sample of what the client is looking for:
http://velmorati.it/
Pages to include:
• Home – A nice slider design to showcase selected photos
• Main Category Template
• Sub Category Template
• About us
• Contact us
Example of their Main Categories and their Sub Categories:
Collections - Granite
- Marble
- Sculpture
Projects - Private
- Public
- Commercial
- Overseas
Installation - Vanity tops
- Hall areas
- Toilets
The Main Category is to show a sample and link the user to the respective Sub Categories. The Sub Categories are to showcase all the photos they have from the category. Please leave a little space to add some text or caption for the photo.
Designs need to be mobile responsive!
I've attached their logo and some sample photos to use for mock ups. Let me know if you have any questions!

```html
<!DOCTYPE html>
<html lang="en">
<head>
<meta charset="utf-8">
<title>Rockvale — Home</title>
<link href="https://fonts.googleapis.com/css2?family=Roboto:wght@400;500&display=swap" rel="stylesheet">
<style>
:root{
  --red:#c8170b;
  --white:#ffffff;
  --ink:#000000;
  --header-bg:rgba(25,25,25,.6);
  --band-bg:rgba(0,0,0,.58);
  --logo-bg:#c9c9c9;
  --muted:#e8e8e8;
}
*{box-sizing:border-box;margin:0;padding:0}
html,body{width:1200px;height:673px;overflow:hidden;background:var(--ink)}
body{position:relative;font-family:'Roboto',Arial,sans-serif;color:var(--white)}

.hero{position:absolute;left:0;top:0;width:1200px;height:592px;
  background:
    radial-gradient(ellipse 120px 90px at 820px 260px,rgba(255,244,214,.55),rgba(255,244,214,0) 70%),
    radial-gradient(ellipse 90px 60px at 230px 125px,rgba(255,236,180,.45),rgba(255,236,180,0) 70%),
    linear-gradient(180deg,rgba(0,0,0,0) 0%,rgba(0,0,0,0) 62%,rgba(20,18,16,.75) 78%,rgba(10,9,8,.95) 100%),
    linear-gradient(90deg,#1c1d1a 0%,#2f302b 12%,#5f5d58 22%,#8c8985 34%,#56514b 44%,#3a3733 52%,#a5a19a 62%,#bdb8b0 74%,#aaa59d 86%,#3d3a36 94%,#1a1918 100%);}

.site-header{position:absolute;left:0;top:0;width:1200px;height:107px;background:var(--header-bg)}
.brand{position:absolute;left:88px;top:0;width:212px;height:107px;background:var(--logo-bg);
  display:flex;align-items:center;justify-content:center;gap:10px;
  color:var(--red);font-weight:500;font-size:24px;letter-spacing:1px;text-decoration:none}
.brand-mark{width:14px;height:14px;background:var(--red)}
.main-nav{position:absolute;top:37px;left:0;width:1200px;height:30px}
.main-nav a{position:absolute;top:0;height:30px;line-height:30px;color:var(--white);text-decoration:none;font-size:13.5px}
.main-nav a.active{background:var(--red);padding:0 8px;border-radius:3px}
.search{position:absolute;left:1083px;top:36px;width:28px;height:28px;border:1.5px solid var(--white);border-radius:50%}
.dropdown{position:absolute;left:540px;top:74px;width:120px;height:105px;background:var(--red);list-style:none;padding-top:10px}
.dropdown li{height:31px;line-height:20px;padding-left:14px;font-size:12.5px;display:flex;align-items:flex-start;gap:7px}
.dropdown svg{margin-top:6px}
.slide-arrow{position:absolute;top:308px}

.band{position:absolute;left:0;top:414px;width:1200px;height:161px;background:var(--band-bg)}
.tab{position:absolute;top:370px;height:44px;background:var(--red);font-size:16px;font-weight:500;
  line-height:46px;padding-left:13px;clip-path:polygon(0 0,78% 0,100% 100%,0 100%)}
.tab-collections{left:88px;width:168px}
.tab-news{left:637px;width:167px}
.tile{position:absolute;top:414px;width:177px;height:161px}
.tile-photo{position:absolute;inset:0}
.tile-caption{position:absolute;left:0;bottom:0;width:100%;height:30px;background:rgba(0,0,0,.55);
  font-size:15px;font-weight:500;line-height:30px;padding-left:11px}
.news-photo{position:absolute;left:641px;top:434px;width:133px;height:116px;
  background:linear-gradient(135deg,#c9a54a,#e4cf86 50%,#a8843a)}
.news-title{position:absolute;left:783px;top:437px;font-size:13.5px;font-weight:400}
.news-body{position:absolute;left:784px;top:465px;width:310px;font-size:11px;line-height:16.7px;color:var(--muted)}
.news-next{position:absolute;left:1064px;top:549px;font-size:10.5px;display:flex;align-items:center;gap:5px}

.site-footer{position:absolute;left:0;top:592px;width:1200px;height:81px;background:var(--ink)}
.footer-links{position:absolute;left:91px;top:20px;font-size:12.5px}
.footer-links span{margin:0 6px}
.copyright{position:absolute;left:91px;top:43px;font-size:12.5px}
.social{position:absolute;top:26px;width:29px;height:29px;border-radius:50%;border:2px solid #d9d9d9}
</style>
</head>
<body>
<div class="hero" role="img" aria-label="Slider photo: elegant dining room and hallway with table lamp, mirrors and plants"></div>

<header class="site-header">
  <a class="brand" href="#"><span class="brand-mark"></span>ROCKVALE</a>
  <nav class="main-nav">
    <a style="left:480px">HOME</a>
    <a class="active" style="left:539px">COLLECTIONS</a>
    <a style="left:661px">PROJECTS</a>
    <a style="left:759px">INSTALLATIONS</a>
    <a style="left:886px">ABOUT US</a>
    <a style="left:981px">CONTACT US</a>
  </nav>
  <div class="search">
    <svg width="25" height="25" viewBox="0 0 25 25"><circle cx="11" cy="11" r="4" fill="none" stroke="#fff" stroke-width="2"/><line x1="14" y1="14" x2="17" y2="17" stroke="#fff" stroke-width="2"/></svg>
  </div>
</header>

<ul class="dropdown">
  <li><svg width="8" height="8" viewBox="0 0 8 8"><path d="M1 1l3 3-3 3M4 1l3 3-3 3" fill="none" stroke="#fff" stroke-width="1.2"/></svg>GRANITE</li>
  <li><svg width="8" height="8" viewBox="0 0 8 8"><path d="M1 1l3 3-3 3M4 1l3 3-3 3" fill="none" stroke="#fff" stroke-width="1.2"/></svg>MARBLE</li>
  <li><svg width="8" height="8" viewBox="0 0 8 8"><path d="M1 1l3 3-3 3M4 1l3 3-3 3" fill="none" stroke="#fff" stroke-width="1.2"/></svg>SCULPTURE</li>
</ul>

<svg class="slide-arrow" style="left:30px" width="24" height="38" viewBox="0 0 24 38"><path d="M20 2L4 19l16 17" fill="none" stroke="rgba(255,255,255,.8)" stroke-width="3"/></svg>
<svg class="slide-arrow" style="left:1144px" width="24" height="38" viewBox="0 0 24 38"><path d="M4 2l16 17L4 36" fill="none" stroke="rgba(255,255,255,.8)" stroke-width="3"/></svg>

<div class="band"></div>
<div class="tab tab-collections">COLLECTIONS</div>
<div class="tab tab-news">LATEST NEWS</div>

<div class="tile" style="left:88px">
  <div class="tile-photo" role="img" aria-label="Mosaic tiled lounge with chairs" style="background:linear-gradient(160deg,#8a7f78,#b8aca2 55%,#6b4a38)"></div>
  <div class="tile-caption">GRANITE</div>
</div>
<div class="tile" style="left:266px">
  <div class="tile-photo" role="img" aria-label="Bathroom with mosaic wall and mirror" style="background:linear-gradient(160deg,#9c7c5c,#d6d4d0 40%,#a9a7a3)"></div>
  <div class="tile-caption">MARBLE</div>
</div>
<div class="tile" style="left:444px">
  <div class="tile-photo" role="img" aria-label="Mosaic tiled room with wooden chair" style="background:linear-gradient(160deg,#6d6d6d,#b4b2ae 50%,#7e7b77)"></div>
  <div class="tile-caption">SCULPTURE</div>
</div>

<div class="news-photo" role="img" aria-label="Chandelier against gold mosaic tiles"></div>
<h2 class="news-title">LOREM IPSUM IS SIMPLY DUMMY TEXT</h2>
<p class="news-body">Lorem Ipsum has been the industry's standard dummy text ever since the 1500s, when an unknown printer took a galley of type and scrambled it to make a type specimen book. It has survived not only five centuries, but also the leap into electronic</p>
<div class="news-next">Next <svg width="11" height="10" viewBox="0 0 11 10"><path d="M1 1l4 4-4 4M6 1l4 4-4 4" fill="none" stroke="#fff" stroke-width="1.6"/></svg></div>

<footer class="site-footer">
  <div class="footer-links">HOME<span>|</span>ABOUT<span>|</span>NEWS<span>|</span>BLOG<span>|</span>CONTACTS</div>
  <div class="copyright">Copyrights © 2014 &nbsp;|&nbsp; Privacy Policy</div>
  <div class="social" style="left:971px;background:#3b5a99"></div>
  <div class="social" style="left:1007px;background:#c43a2f"></div>
  <div class="social" style="left:1043px;background:#1f9fde"></div>
  <div class="social" style="left:1080px;background:#f06416"></div>
</footer>
</body>
</html>
```